Business Card Design Project

This is the first time we use our new logo. We need a business card that we can use both on our institutional corporate relationships and also that works for our staff that deals with consumers directly.

VELUNDA is a new company dedicated to empower consumers and to provide them with the best choices for specialized health care using the latest telemedicine technology (medicine at a distance via videoconference).

We want to print this cards in high quality materials and process. We will like designs that allow us to use UV spot varnish and other techniques that will differentiate us.

We are including Two different versions of Color logos. In addition we are including white over black background logos. Those can be used replacing the black for a color.

Please note this is the first time we will be creating any corporate materials with our new logo and colors.

Target Market(s)

34+ consumers of medium high and high socioeconomic levels.

Industry/Entity Type

Health

Requirements
Must have
• Our logo on its original colors
Should not have
• Any other graphical element or design that is not our logo

```html
<!DOCTYPE html>
<html lang="en">
<head>
<meta charset="utf-8">
<title>VELUNDA Business Card</title>
<link rel="stylesheet" href="https://fonts.googleapis.com/css2?family=Montserrat:wght@600&family=Arimo:wght@400&display=swap">
<style>
  :root {
    --stage: #ecebf0;
    --sky: #57b4de;
    --navy: #1c5a87;
    --teal: #2aa89a;
    --white: #ffffff;
    --ink: #1d3550;
  }
  html, body {
    margin: 0;
    padding: 0;
    width: 1200px;
    height: 987px;
    overflow: hidden;
    background: var(--stage);
  }
  .canvas {
    position: relative;
    width: 1200px;
    height: 987px;
  }
  .card {
    position: absolute;
    top: 336px;
    width: 540px;
    height: 315px;
    border-radius: 26px;
    overflow: hidden;
    box-shadow: 0 6px 18px rgba(0,0,0,0.12);
  }
  .card-front { left: 40px; background: var(--white); }
  .card-back { left: 620px; background: var(--sky); }

  .front-wave {
    position: absolute;
    inset: 0;
    width: 540px;
    height: 315px;
  }
  .brand-lockup {
    position: absolute;
    left: 150px;
    top: 52px;
    display: flex;
    align-items: center;
    gap: 14px;
  }
  .brand-dot {
    width: 30px;
    height: 30px;
    border-radius: 50%;
    background: var(--navy);
  }
  .brand-name {
    font-family: "Montserrat", sans-serif;
    font-weight: 600;
    font-size: 48px;
    letter-spacing: 3px;
    color: var(--navy);
    line-height: 1;
  }
  .holder {
    position: absolute;
    left: 196px;
    top: 128px;
    font-family: "Arimo", sans-serif;
    font-size: 19px;
    color: var(--navy);
    font-weight: 700;
  }
  .holder .role {
    color: var(--teal);
    font-weight: 400;
  }
  .contact {
    position: absolute;
    left: 24px;
    font-family: "Arimo", sans-serif;
    font-size: 14px;
    color: var(--ink);
    display: flex;
    align-items: center;
    gap: 6px;
    white-space: nowrap;
  }
  .contact svg { width: 11px; height: 11px; }
  .contact-phones { top: 232px; }
  .contact-web { top: 256px; }
  .contact-address { top: 280px; }

  .back-lockup {
    position: absolute;
    left: 0;
    right: 0;
    top: 112px;
    display: flex;
    justify-content: center;
    align-items: center;
    gap: 16px;
  }
  .back-lockup .brand-dot { background: var(--white); width: 34px; height: 34px; }
  .back-lockup .brand-name { color: var(--white); font-size: 52px; }
  .back-url {
    position: absolute;
    left: 0;
    right: 0;
    top: 196px;
    text-align: center;
    font-family: "Arimo", sans-serif;
    font-size: 16px;
    letter-spacing: 5px;
    color: var(--white);
  }
</style>
</head>
<body>
<main class="canvas">
  <section class="card card-front">
    <svg class="front-wave" viewBox="0 0 540 315" aria-hidden="true">
      <path d="M0,118 C160,170 360,228 540,292 L540,315 L0,315 Z" fill="var(--sky)"/>
      <path d="M0,118 C160,170 360,228 540,292" fill="none" stroke="var(--navy)" stroke-width="7"/>
    </svg>
    <div class="brand-lockup">
      <span class="brand-dot"></span>
      <span class="brand-name">VELUNDA</span>
    </div>
    <div class="holder">Your Name, <span class="role">Title</span></div>

    <div class="contact contact-phones">
      <svg viewBox="0 0 12 12"><circle cx="6" cy="6" r="6" fill="var(--navy)"/><path d="M4 3.2 L5.2 4.6 L4.6 5.4 Q5.6 7 6.6 7.4 L7.4 6.8 L8.8 8 L8 9 Q5 8.6 3.2 4 Z" fill="var(--white)"/></svg>
      012-345-6789
      <svg viewBox="0 0 12 12"><circle cx="6" cy="6" r="6" fill="var(--navy)"/><path d="M4 3.2 L5.2 4.6 L4.6 5.4 Q5.6 7 6.6 7.4 L7.4 6.8 L8.8 8 L8 9 Q5 8.6 3.2 4 Z" fill="var(--white)"/></svg>
      012-345-6789
    </div>
    <div class="contact contact-web">
      <svg viewBox="0 0 12 12"><circle cx="6" cy="6" r="6" fill="var(--navy)"/><rect x="2.8" y="3.8" width="6.4" height="4.4" fill="none" stroke="var(--white)" stroke-width="0.9"/><path d="M2.8 3.8 L6 6.4 L9.2 3.8" fill="none" stroke="var(--white)" stroke-width="0.9"/></svg>
      name@velunda.com
      <svg viewBox="0 0 12 12"><circle cx="6" cy="6" r="6" fill="var(--navy)"/><circle cx="6" cy="6" r="3.6" fill="none" stroke="var(--white)" stroke-width="0.8"/><path d="M2.4 6 H9.6 M6 2.4 V9.6" stroke="var(--white)" stroke-width="0.8"/></svg>
      www.velunda.com
    </div>
    <div class="contact contact-address">Street Name, City Name, State, City Zip Code</div>
  </section>

  <section class="card card-back">
    <div class="back-lockup">
      <span class="brand-dot"></span>
      <span class="brand-name">VELUNDA</span>
    </div>
    <div class="back-url">www.velunda.com</div>
  </section>
</main>
</body>
</html>
```